Dietitian/Nutritionist seeks trifold marketing brochure

We need a trifold brochure for marketing to patients within a doctors surgery. This will be a source of information for prospective patients, what they can expect and how to contact us. The brochure needs to have some key information such as a brief description of the services available, fees, locations of clinics and contact information. Our current brochure has been uploaded which has the information you need to complete this project. The files you provide will allow us to edit the information at a later date as pricing and services change.

Target Market(s)

Patients who have been referred to see a dietitian/nutritionist and people who are considering seeing a dietitian/nutritionist but haven't decided

Industry/Entity Type

Dietician

Font styles to use
Serif

Colors

Designer to choose colors to be used in the design.

Requirements
Must have
• My logo
• Accredited practising dietitian logo
• My website address and contact details
• Most of the information that is in my current brochure
• Locations/names of the four clinics
Nice to have
• Images that promote cooking, health and wellbeing

```html
<!DOCTYPE html>
<html lang="en">
<head>
<meta charset="utf-8">
<title>Northview Nutrition – Trifold Brochure</title>
<link rel="stylesheet" href="https://fonts.googleapis.com/css2?family=Lato:wght@400;700;900&family=Oswald:wght@500;600&display=swap">
<style>
  :root{
    --green:#7cbb3a;
    --green-dark:#5f9a25;
    --orange:#f07c1f;
    --ink:#1d1d1d;
    --grey:#8a8a8a;
    --path:#d4d4d4;
    --paper:#ffffff;
    --backdrop:#e6e6e6;
  }
  *{box-sizing:border-box;margin:0;padding:0}
  html,body{width:1055px;height:1200px;overflow:hidden}
  body{background:var(--backdrop);font-family:"Lato",sans-serif;color:var(--ink);position:relative}
  .brochure{position:absolute;left:10px;top:200px;width:1035px;height:800px;display:flex;box-shadow:0 6px 24px rgba(0,0,0,.18)}
  .panel{width:345px;height:800px;position:relative}

  /* Panel 1 – about */
  .panel--about{background:var(--green);color:#fff;padding:38px 30px}
  .about-intro{font-size:14px;line-height:1.45;font-weight:700}
  .about-intro strong{font-weight:900}
  .section-head{display:flex;align-items:center;gap:14px;margin-top:34px}
  .section-head svg{flex:none}
  .section-title{font-family:"Oswald",sans-serif;font-weight:500;font-size:26px;letter-spacing:1px}
  .section-text{font-size:14px;line-height:1.4;margin:6px 0 0 58px}
  .locations{list-style:none;margin:14px 0 0 30px;border-left:2px solid #fff;padding-left:22px}
  .locations li{position:relative;font-size:14px;line-height:1.35;margin-bottom:18px}
  .locations li::before{content:"";position:absolute;left:-31px;top:3px;width:14px;height:14px;border-radius:50%;background:var(--ink);border:2px solid #fff}

  /* Panel 2 – services */
  .panel--services{background:var(--paper);padding:36px 22px}
  .services-title{font-family:"Oswald",sans-serif;font-weight:500;color:var(--green);font-size:17px;line-height:1.25;letter-spacing:.5px}
  .services-path{margin-top:22px;display:block}
  .services-path .node-num{fill:#fff;font-size:12px;font-weight:900}
  .services-path .label{font-size:10px;font-weight:900}
  .services-path .desc{fill:var(--grey);font-size:9px;font-weight:400}
  .contact{position:absolute;left:22px;right:22px;bottom:120px;font-size:11px;line-height:1.6;color:var(--ink)}
  .contact strong{color:var(--green-dark);font-weight:900}
  .services-brands{position:absolute;left:22px;right:22px;bottom:36px;display:flex;justify-content:space-between;align-items:center}
  .brand-name{display:flex;align-items:center;gap:8px;font-weight:900;font-size:18px;color:var(--green-dark)}
  .brand-name .dot{width:18px;height:18px;border-radius:50%;background:var(--green-dark)}
  .partner-badge{width:84px;height:58px;background:var(--orange);border-radius:4px}

  /* Panel 3 – fees */
  .panel--fees{background:var(--paper)}
  .food-photo{height:250px;background:linear-gradient(135deg,#5a4638 0%,#3f6b2c 45%,#7aa33e 70%,#c9c4b6 100%)}
  .fees{position:absolute;left:40px;top:300px;width:265px}
  .fees-cap{height:120px;background:var(--green);border-radius:132px 132px 0 0;display:flex;align-items:flex-end;justify-content:center;padding-bottom:18px;color:#fff;font-family:"Oswald",sans-serif;font-size:34px;font-weight:600;letter-spacing:1px}
  .fee{display:flex;align-items:center;gap:12px;padding:12px 18px;color:#fff;margin:0 auto}
  .fee-num{font-family:"Oswald",sans-serif;font-size:28px;font-weight:600;flex:none}
  .fee-text{font-size:11px;line-height:1.35}
  .fee--1{background:var(--orange);width:100%}
  .fee--2{background:var(--ink);width:88%}
  .fee--3{background:var(--green);width:72%;border-radius:0 0 40px 40px;padding-bottom:22px}
</style>
</head>
<body>
<div class="brochure">

  <section class="panel panel--about">
    <p class="about-intro"><strong>Accredited Practising Dietitians (APDs) are University trained experts in food and nutrition,</strong> they are able to translate the latest scientific evidence into sensible and practical advice. Dietitians differ from nutritionists as they have specific training in clinical environments such as hospitals. This training allows a dietitian to interpret blood tests, understand any food and medication interactions, and communicate with other health professionals involved in your care.</p>

    <div class="section-head">
      <svg width="44" height="44" viewBox="0 0 44 44" aria-hidden="true"><g fill="none" stroke="#fff" stroke-width="2.5" stroke-linecap="round"><path d="M22 10a10 10 0 0 0-6 18v5h12v-5a10 10 0 0 0-6-18z"/><path d="M17 37h10M18 40h8M22 2v3M8 8l2 2M36 8l-2 2M4 20h3M40 20h-3"/></g></svg>
      <h2 class="section-title">BENEFIT</h2>
    </div>
    <p class="section-text">Seeing a dietitian for the first time involves working with you to develop strategies and goals to improve your health.</p>

    <div class="section-head">
      <svg width="44" height="44" viewBox="0 0 44 44" aria-hidden="true"><path d="M22 3a13 13 0 0 0-13 13c0 10 13 25 13 25s13-15 13-25A13 13 0 0 0 22 3zm0 18a5 5 0 1 1 0-10 5 5 0 0 1 0 10z" fill="#fff"/></svg>
      <h2 class="section-title">LOCATIONS</h2>
    </div>
    <ul class="locations">
      <li>Hillcrest Medical Centre - Fridays</li>
      <li>Brookfield Medical - Wednesday</li>
      <li>Riverbend Health Clinic - Thursday</li>
      <li>Eastwood Doctors Surgery - Approximately every 4 weeks</li>
    </ul>
  </section>

  <section class="panel panel--services">
    <h2 class="services-title">ACCREDITED PRACTISING DIETITIANS<br>CAN ASSIST YOU WITH</h2>
    <svg class="services-path" width="301" height="420" viewBox="0 0 301 420" font-family="Lato, sans-serif">
      <path d="M20 40 H130 a35 35 0 0 1 0 70 H60 a35 35 0 0 0 0 70 H130 a35 35 0 0 1 0 70 H60 a35 35 0 0 0 0 70 H130 a35 35 0 0 1 0 70 H20" fill="none" stroke="var(--path)" stroke-width="8"/>

      <circle cx="60" cy="40" r="17" fill="var(--green)"/><text class="node-num" x="60" y="44" text-anchor="middle">01</text>
      <text class="label" x="178" y="33" fill="var(--green)">DIABETES</text>
      <text class="desc" x="178" y="46">Type 1 &amp; 2, prediabetes</text>
      <text class="desc" x="178" y="57">and gestational diabetes</text>

      <circle cx="130" cy="110" r="17" fill="var(--green)"/><text class="node-num" x="130" y="114" text-anchor="middle">02</text>
      <text class="label" x="178" y="103" fill="var(--green)">DIGESTIVE HEALTH</text>
      <text class="desc" x="178" y="116">IBS, coeliac disease,</text>
      <text class="desc" x="178" y="127">reflux and intolerance</text>

      <circle cx="60" cy="180" r="17" fill="var(--ink)"/><text class="node-num" x="60" y="184" text-anchor="middle">03</text>
      <text class="label" x="178" y="173" fill="var(--ink)">GASTRIC BANDING</text>
      <text class="desc" x="178" y="186">Pre and post surgical</text>
      <text class="desc" x="178" y="197">weight loss support</text>

      <circle cx="130" cy="250" r="17" fill="var(--orange)"/><text class="node-num" x="130" y="254" text-anchor="middle">04</text>
      <text class="label" x="178" y="243" fill="var(--orange)">CHOLESTEROL</text>
      <text class="desc" x="178" y="256">Heart health and</text>
      <text class="desc" x="178" y="267">blood pressure</text>

      <circle cx="60" cy="320" r="17" fill="var(--green)"/><text class="node-num" x="60" y="324" text-anchor="middle">05</text>
      <text class="label" x="178" y="313" fill="var(--green)">WEIGHT MANAGEMENT</text>
      <text class="desc" x="178" y="326">Weight loss, gain</text>
      <text class="desc" x="178" y="337">and healthy habits</text>

      <circle cx="130" cy="390" r="17" fill="var(--ink)"/><text class="node-num" x="130" y="394" text-anchor="middle">06</text>
      <text class="label" x="178" y="383" fill="var(--ink)">GENERAL</text>
      <text class="desc" x="178" y="396">Healthy eating</text>
      <text class="desc" x="178" y="407">and nutrition</text>
    </svg>

    <address class="contact">
      <strong>Phone</strong> 03 5550 1234<br>
      <strong>Email</strong> hello@northviewnutrition.com.au<br>
      <strong>Web</strong> www.northviewnutrition.com.au
    </address>

    <div class="services-brands">
      <div class="brand-name"><span class="dot"></span>Northview Nutrition</div>
      <div class="partner-badge" role="img" aria-label="Accreditation badge"></div>
    </div>
  </section>

  <section class="panel panel--fees">
    <div class="food-photo" role="img" aria-label="Photo of a fresh green salad in a bowl on a wooden table"></div>
    <div class="fees">
      <div class="fees-cap">$ FEES</div>
      <div class="fee fee--1"><span class="fee-num">01</span><p class="fee-text">Initial consultation (60 mins): $120. Medicare rebates apply with a GP care plan.</p></div>
      <div class="fee fee--2"><span class="fee-num">02</span><p class="fee-text">Follow-up consultation (30 mins): $70. Private health rebates available on the spot.</p></div>
      <div class="fee fee--3"><span class="fee-num">03</span><p class="fee-text">Group sessions and programs: fees on request. Please ask reception.</p></div>
    </div>
  </section>

</div>
</body>
</html>
```